Realty Group Needs Classy, Contemporary Letterhead Design

We need a letterhead design for a new realty company located in NY, USA. We buy investment properties to rehabilitate and or keep in our rental portfolio.

```html
<!DOCTYPE html>
<html lang="en">
<head>
<meta charset="utf-8">
<title>Northgate Realty Group — Letterhead</title>
<link href="https://fonts.googleapis.com/css2?family=Didact+Gothic&family=Montserrat:wght@700&display=swap" rel="stylesheet">
<style>
  :root {
    --brand: #4a2a8c;
    --ink: #2b2b2b;
    --muted: #5a5a5a;
    --rule: #3a3a3a;
    --paper: #f1f1f1;
    --paper-edge: #e6e6e6;
  }
  * { margin: 0; padding: 0; box-sizing: border-box; }
  html, body { width: 960px; height: 1200px; overflow: hidden; }
  body { background: var(--paper); font-family: "Didact Gothic", sans-serif; color: var(--ink); }
  .letterhead {
    position: relative; width: 960px; height: 1200px;
    background: linear-gradient(90deg, var(--paper) 0%, #ececec 60%, var(--paper-edge) 100%);
  }
  .brand {
    position: absolute; top: 112px; left: 0; width: 100%;
    display: flex; justify-content: center; align-items: center; gap: 12px;
  }
  .brand-dot { width: 18px; height: 18px; border-radius: 50%; background: var(--brand); }
  .brand-name {
    font-family: "Montserrat", sans-serif; font-weight: 700; font-size: 30px;
    color: var(--brand); letter-spacing: 0.5px;
  }
  .letter { position: absolute; left: 87px; top: 350px; width: 791px; }
  .salutation { font-size: 21px; margin-bottom: 34px; }
  .letter p.body {
    font-size: 13px; line-height: 19px; text-align: justify; color: var(--ink);
    margin-bottom: 19px;
  }
  .closing { font-size: 13px; margin-top: 30px; }
  .signature {
    display: block; margin-top: 26px; width: 130px; height: 62px;
    background: linear-gradient(90deg, #dcdcdc, #e8e8e8); border-radius: 4px;
  }
  .contact { position: absolute; left: 87px; top: 1027px; font-size: 14px; line-height: 19px; }
  .contact li { list-style: none; display: flex; align-items: center; gap: 8px; }
  .contact svg { width: 11px; height: 11px; fill: var(--brand); }
  .address { position: absolute; right: 82px; top: 1046px; text-align: right; font-size: 14px; line-height: 17px; }
  .address .pin { width: 10px; height: 12px; fill: var(--brand); vertical-align: -1px; }
  .footer-rule { position: absolute; left: 87px; right: 82px; top: 1113px; border-top: 1px solid var(--rule); }
  .website {
    position: absolute; left: 89px; top: 1128px;
    font-family: "Montserrat", sans-serif; font-weight: 700; font-size: 13.5px; color: var(--brand);
  }
</style>
</head>
<body>
<main class="letterhead">
  <header class="brand">
    <span class="brand-dot"></span>
    <span class="brand-name">Northgate Realty Group, LLC</span>
  </header>

  <section class="letter">
    <p class="salutation">Dear Mr. Harlow,</p>
    <p class="body">Lorem ipsum dolor sit amet, consectetur adipiscing elit. Donec orci purus, luctus vitae dignissim eu, iaculis sed purus. Vivamus faucibus, ipsum nec aliquet viverra, leo mauris condimentum ligula, sit amet sagittis enim ligula quis arcu. Nam egestas tortor id nisi porttitor mattis. In tortor ante, ultricies in suscipit a, tempus non massa. Vivamus et auctor mi. Fusce vel massa nulla. Phasellus nec eros mauris, et scelerisque orci.</p>
    <p class="body">Donec malesuada orci vitae nulla accumsan porta a id massa. Quisque accumsan iaculis magna sit amet fringilla. Maecenas consequat, magna eget tincidunt semper, odio nibh rutrum mi, id feugiat ante nisi eu risus. Vestibulum nunc orci, rhoncus a placerat in, ultricies in mi. Cras mattis varius eros, vel fringilla nisi suscipit eget. Quisque scelerisque sagittis nulla at porttitor.</p>
    <p class="body">Sed id augue vitae urna euismod commodo aliquet a quam. Pellentesque arcu velit, cursus et malesuada ut, consequat et diam. Nullam erat sem, rhoncus id ullamcorper vitae, rhoncus et arcu. In ultricies ultricies nulla, ut rutrum nisi iaculis at. Donec eu magna a metus ornare faucibus. Fusce aliquet faucibus ultricies. Morbi semper, est id tincidunt gravida, sem arcu adipiscing lacus, ac bibendum nulla leo eu purus. Quisque nec diam sed risus consectetur accumsan quis quis nibh. Vestibulum id purus lorem.</p>
    <p class="body">It is a long established fact that a reader will be distracted by the readable content of a page when looking at its layout. The point of using Lorem Ipsum is that it has a more-or-less normal distribution of letters, as opposed to using 'Content here, content here', making it look like readable English. Many desktop publishing packages</p>
    <p class="closing">Sincerely,</p>
    <span class="signature" role="img" aria-label="Handwritten signature of the sender"></span>
  </section>

  <ul class="contact">
    <li><svg viewBox="0 0 24 24"><path d="M6.6 10.8a15.1 15.1 0 0 0 6.6 6.6l2.2-2.2c.3-.3.7-.4 1-.2 1.1.4 2.3.6 3.6.6.6 0 1 .4 1 1V20c0 .6-.4 1-1 1A17 17 0 0 1 3 4c0-.6.4-1 1-1h3.5c.6 0 1 .4 1 1 0 1.3.2 2.5.6 3.6.1.3 0 .7-.2 1z"/></svg>555-214-3870</li>
    <li><svg viewBox="0 0 24 24"><path d="M7 1h10a2 2 0 0 1 2 2v18a2 2 0 0 1-2 2H7a2 2 0 0 1-2-2V3a2 2 0 0 1 2-2zm0 3v14h10V4z"/></svg>555-631-9042</li>
    <li><svg viewBox="0 0 24 24"><path d="M6 2h12v5H6zM3 8h18a2 2 0 0 1 2 2v7h-4v5H5v-5H1v-7a2 2 0 0 1 2-2zm4 8v4h10v-4z"/></svg>555-408-1756</li>
    <li><svg viewBox="0 0 24 24"><path d="M2 5h20v14H2zm2 2v.5l8 5 8-5V7z"/></svg>info@northgaterealty.com</li>
  </ul>

  <address class="address" style="font-style:normal">
    <svg class="pin" viewBox="0 0 20 24"><path d="M10 0a8 8 0 0 0-8 8c0 6 8 16 8 16s8-10 8-16a8 8 0 0 0-8-8zm0 11a3 3 0 1 1 0-6 3 3 0 0 1 0 6z"/></svg> northgate LLC<br>
    1420 Alder Street<br>
    Albany, New York 12207
  </address>

  <div class="footer-rule"></div>
  <p class="website">WWW.NORTHGATEREALTY.COM</p>
</main>
</body>
</html>
```